Vantiqo custom business card design

Need a authentic, innovative business card design for a new mobile app business. I am uploading a few screen images from our app for you to view. I would like app design theme to match business card design. I can also send logo images.

```html
<!DOCTYPE html>
<html lang="en">
<head>
<meta charset="UTF-8">
<title>Vantiqo Business Card</title>
<link href="https://fonts.googleapis.com/css2?family=Jost:wght@400;500;700&display=swap" rel="stylesheet">
<style>
  :root {
    --purple: #63008f;
    --ink: #1f1f1f;
    --muted: #3a3a3a;
    --paper: #ffffff;
    --backdrop: #e6e6e8;
  }
  * { margin: 0; padding: 0; box-sizing: border-box; }
  html, body {
    width: 1200px;
    height: 874px;
    overflow: hidden;
    background: var(--backdrop);
    font-family: "Jost", sans-serif;
  }
  .canvas {
    position: relative;
    width: 1200px;
    height: 874px;
  }
  .card {
    position: absolute;
    left: 320px;
    width: 560px;
    height: 320px;
    box-shadow: 0 6px 18px rgba(0,0,0,0.18);
  }
  /* Front */
  .card-front {
    top: 77px;
    background: var(--purple);
    color: var(--paper);
  }
  .front-brand {
    position: absolute;
    left: 0; right: 0;
    top: 78px;
    display: flex;
    flex-direction: column;
    align-items: center;
    gap: 14px;
  }
  .front-brand .brand-dot {
    width: 86px; height: 86px;
    border-radius: 50%;
    background: var(--paper);
  }
  .front-brand .brand-name {
    font-weight: 700;
    font-size: 34px;
    letter-spacing: 1px;
    color: var(--paper);
  }
  .front-url {
    position: absolute;
    left: 0; right: 0;
    bottom: 34px;
    text-align: center;
    font-size: 15px;
    letter-spacing: 8px;
    color: var(--paper);
  }
  /* Back */
  .card-back {
    top: 437px;
    background: var(--paper);
    color: var(--ink);
  }
  .back-brand {
    position: absolute;
    left: 44px;
    top: 62px;
    width: 230px;
    display: flex;
    flex-direction: column;
    align-items: center;
    gap: 12px;
  }
  .back-brand .brand-dot {
    width: 130px; height: 130px;
    border-radius: 50%;
    background: var(--purple);
  }
  .back-brand .brand-name {
    font-weight: 700;
    font-size: 44px;
    line-height: 1;
    color: var(--ink);
  }
  .contact {
    position: absolute;
    left: 318px;
    top: 52px;
    width: 212px;
  }
  .person-name {
    font-weight: 500;
    font-size: 24px;
    line-height: 1;
    color: var(--purple);
  }
  .person-role {
    font-weight: 500;
    font-size: 15px;
    margin-top: 3px;
    color: var(--ink);
  }
  .person-email {
    font-size: 14px;
    color: var(--muted);
    margin-top: 2px;
  }
  .divider {
    border: none;
    border-top: 1.5px dotted #555;
    margin: 12px 0;
  }
  .contact-lines {
    font-size: 15px;
    line-height: 1.35;
    color: var(--muted);
  }
  .contact-url {
    letter-spacing: 3px;
  }
</style>
</head>
<body>
<main class="canvas">
  <section class="card card-front" aria-label="Card front">
    <div class="front-brand">
      <span class="brand-dot" aria-hidden="true"></span>
      <span class="brand-name">Vantiqo</span>
    </div>
    <p class="front-url">www.vantiqo.com</p>
  </section>

  <section class="card card-back" aria-label="Card back">
    <div class="back-brand">
      <span class="brand-dot" aria-hidden="true"></span>
      <span class="brand-name">Vantiqo</span>
    </div>
    <div class="contact">
      <p class="person-name">DANIEL REYES</p>
      <p class="person-role">CEO/FOUNDER</p>
      <p class="person-email">daniel@vantiqo.com</p>
      <hr class="divider">
      <div class="contact-lines">
        <p>Tel: 555 210 4821</p>
        <p>Mob: 555 384 7190</p>
        <p>Fax: 555 672 3058</p>
      </div>
      <hr class="divider">
      <div class="contact-lines">
        <p>4120 Willow Crest Road</p>
        <p>Juneau, Alaska 99801</p>
        <p class="contact-url">www.vantiqo.com</p>
      </div>
    </div>
  </section>
</main>
</body>
</html>
```